Professional Business card

I need a business card to send with all my shipments. It needs to look very professional as I am branding myself, more than I am branding my company. The website is not active yet but that along with the instagram is very important as this will be moving shortly. The next required to be included is listed

Target Market(s)

All

Contact Information for Business Card

Very professional and sleek, I am trying to look like the CEO, motivational speaker and future president I plan to be

Colors
ffcf3e

Requirements
Must have
• Front

Dale Wrenfield
CEO
Brivolt Franchiser
Business Consultant/Start Up Guidance
Motivational Speaker
President of The United States 2040
www.dalewrenfield-example.com
[Instagram] @dalewrenfield

Back
I teach the success method used by my company you just bought from. Learn the unique model and start your own Brivolt franchise today
Nice to have
• Black and Gold lettering
Should not have
• Playful vibes

```html
<!DOCTYPE html>
<html lang="en">
<head>
<meta charset="utf-8">
<title>Dale Wrenfield – Business Card</title>
<link rel="stylesheet" href="https://fonts.googleapis.com/css2?family=Poppins:wght@400;500;600&display=swap">
<style>
  :root {
    --stage: #262628;
    --card: #050505;
    --gold: #ffcf3e;
    --ink: #ffffff;
  }
  * { margin: 0; padding: 0; box-sizing: border-box; }
  html, body {
    width: 1200px; height: 800px; overflow: hidden;
    background: var(--stage);
    font-family: "Poppins", sans-serif;
  }
  .sheet {
    width: 1200px; height: 800px;
    display: flex; align-items: center; justify-content: center; gap: 40px;
  }
  .card {
    position: relative;
    width: 540px; height: 309px;
    background: var(--card);
    box-shadow: 0 14px 30px rgba(0,0,0,.45);
    color: var(--ink);
    text-align: center;
  }
  .card-frame { position: absolute; inset: 0; width: 100%; height: 100%; }
  .card-frame path { fill: none; stroke: var(--gold); stroke-width: 1.6; }
  .card-body {
    position: absolute; inset: 0;
    display: flex; flex-direction: column; align-items: center; justify-content: center;
    padding: 40px 60px;
  }
  .card--back .card-body { justify-content: flex-start; padding-top: 92px; }
  .pitch { font-size: 15px; font-weight: 500; line-height: 1.3; }
  .holder-name {
    color: var(--gold); font-size: 25px; font-weight: 600;
    letter-spacing: .5px; text-transform: uppercase; line-height: 1.2;
  }
  .roles { list-style: none; font-size: 14px; line-height: 1.3; margin-top: 2px; }
  .website { font-size: 14px; letter-spacing: 3px; margin-top: 10px; }
  .social {
    display: flex; align-items: center; gap: 6px;
    font-size: 14px; margin-top: 2px;
  }
  .social-dot {
    width: 15px; height: 15px; border-radius: 50%;
    background: var(--gold); display: inline-block;
  }
</style>
</head>
<body>
<main class="sheet">

  <section class="card card--back" aria-label="Card back">
    <svg class="card-frame" viewBox="0 0 540 309" aria-hidden="true">
      <path d="M36,20 H504 A16,16 0 0 0 520,36 V273 A16,16 0 0 0 504,289 H36 A16,16 0 0 0 20,273 V36 A16,16 0 0 0 36,20 Z"/>
      <path d="M40,26 H500 A14,14 0 0 0 514,40 V269 A14,14 0 0 0 500,283 H40 A14,14 0 0 0 26,269 V40 A14,14 0 0 0 40,26 Z"/>
    </svg>
    <div class="card-body">
      <p class="pitch">I teach the success method used by my company<br>you just bought from.<br>Learn the unique model and start your<br>own Brivolt franchise today</p>
    </div>
  </section>

  <section class="card card--front" aria-label="Card front">
    <svg class="card-frame" viewBox="0 0 540 309" aria-hidden="true">
      <path d="M36,20 H504 A16,16 0 0 0 520,36 V273 A16,16 0 0 0 504,289 H36 A16,16 0 0 0 20,273 V36 A16,16 0 0 0 36,20 Z"/>
      <path d="M40,26 H500 A14,14 0 0 0 514,40 V269 A14,14 0 0 0 500,283 H40 A14,14 0 0 0 26,269 V40 A14,14 0 0 0 40,26 Z"/>
    </svg>
    <div class="card-body">
      <h1 class="holder-name">Dale Wrenfield</h1>
      <ul class="roles">
        <li>CEO</li>
        <li>Brivolt Franchiser</li>
        <li>Business Consultant/Start Up Guidance</li>
        <li>Motivational Speaker</li>
        <li>President of The United States 2040</li>
      </ul>
      <p class="website">www.dalewrenfield-example.com</p>
      <p class="social"><span class="social-dot" aria-hidden="true"></span>@dalewrenfield</p>
    </div>
  </section>

</main>
</body>
</html>
```